Web landing page design

- Create a Web Design (Uncoded - PSD layout only)

We need a single web page design to promote our service. This page will
acts as a landing page for users and also be utilized in social media
advertising. Please provide us with a cutting edge design. I have attached
a link for what the company is about. In essence we are a photo checking
service which reviews photos for retailers, hotels abd car dealerships to
check everything is good after a service has been performed. Whether it be
a new promotion, cleaning or just checking prices. I am looking for a
design to say that we do many photos and at a very cost effective price
(team based in Mexico)

Link: https://slidevault.example/view/qTr8nWx2LpZk4mHcYdJs/
*Deadline*
5 days
*Updates*

- The Start Here box needs to look like this:

-Start Here (heading)
-A box for email addresses to be entered
-Then a check box with "Yes, I have read and agree to the Privacy Policy
and agree to receive email marketing from Plumora88'
-A submit button

All of this information needs to be in one box please. And please feel
free to contact me if you have any questions about this.

*Target Market(s)*
Retail business, Merchandising companies, Rental property owners, Car
dealers
Updates

Please can you submit entries. I am just looking for a tidy to a presentation already created. Just needs design touches.

Target Market(s)

Ability for audience to understand concept quickly
Benefits to why to use the product stand out
Technology driven approach

Industry/Entity Type

Retail

Number of Pages Required

1 page

Colors
0792cd

Requirements
Must have
• Clean and modern design

```html
<!DOCTYPE html>
<html lang="en">
<head>
<meta charset="utf-8">
<title>Checkora – Transform retail execution</title>
<link href="https://fonts.googleapis.com/css2?family=Lato:ital,wght@0,400;0,700;0,900;1,700&family=Open+Sans:ital,wght@0,400;0,600;0,700;1,600&display=swap" rel="stylesheet">
<style>
:root{
  --blue:#0792cd;
  --blue-band:#3aa3dc;
  --ink:#222;
  --muted:#666;
  --line:#d9d9d9;
  --dark:#2b2d30;
  --white:#fff;
}
*{box-sizing:border-box;margin:0;padding:0}
html,body{width:1200px;height:3191px;overflow:hidden;background:var(--white)}
body{position:relative;font-family:"Open Sans",Arial,sans-serif;color:var(--ink)}
.abs{position:absolute}

/* hero */
.hero{left:0;top:0;width:1200px;height:566px;background:linear-gradient(120deg,#c9b7a2 0%,#8f8a86 35%,#6e87a8 65%,#3f5e86 100%)}
.hero::after{content:"";position:absolute;inset:0;background:rgba(0,0,0,.18)}
.brand{left:98px;top:30px;z-index:2;display:flex;flex-direction:column;align-items:center;gap:6px}
.brand-dot{width:38px;height:38px;border-radius:50%;background:var(--blue)}
.brand-name{font-family:Lato,sans-serif;font-weight:700;font-size:26px;color:var(--white)}
.nav{right:98px;top:54px;z-index:2;display:flex;gap:34px;font-family:Lato,sans-serif;font-weight:700;font-size:17px;color:var(--white);align-items:center}
.nav .active{color:#5cc3f0}
.hero-title{left:0;top:196px;width:1200px;z-index:2;text-align:center;font-family:Lato,sans-serif;font-weight:700;font-size:58px;line-height:74px;color:var(--white)}
.dots{left:568px;top:496px;z-index:2;display:flex;gap:6px}
.dots span{width:12px;height:12px;border-radius:50%;border:2px solid var(--white)}
.dots span:first-child{background:var(--white)}

/* stats */
.stats{left:0;top:566px;width:1102px;height:122px;display:flex;border-bottom:1px solid var(--line)}
.stat{flex:1;border-right:1px solid var(--line);text-align:center;padding-top:22px}
.stat-num{font-family:Lato,sans-serif;font-weight:700;font-size:44px;color:var(--blue);line-height:50px}
.stat-label{font-size:15px;color:var(--muted);margin-top:6px}
.stats-rule{left:0;top:687px;width:1200px;height:1px;background:var(--line)}

/* founder */
.founder-photo{left:96px;top:743px;width:336px;height:336px;border-radius:50%;border:8px solid #eee;background:radial-gradient(circle at 50% 40%,#dde6ef,#b7c6d6)}
.founder-title{left:496px;top:806px;font-family:Lato,sans-serif;font-weight:900;font-size:33px;color:var(--ink)}
.founder-name{left:496px;top:856px;font-family:Lato,sans-serif;font-weight:700;font-size:24px;color:var(--blue)}
.ticks{list-style:none;font-size:15px;color:var(--muted)}
.ticks li{display:flex;align-items:center;gap:14px;height:36px}
.ticks svg{flex:none}
.founder-list{left:496px;top:910px}

/* benefits band */
.band{left:0;top:1132px;width:1200px;height:421px;background:linear-gradient(90deg,#3c9fd6,#49aee2)}
.band-title{left:96px;top:1198px;font-family:Lato,sans-serif;font-weight:900;font-size:32px;line-height:44px;color:var(--white)}
.band-sub{left:96px;top:1306px;font-style:italic;font-weight:600;font-size:18px;color:var(--white)}
.band-list{left:96px;top:1368px;color:var(--white);font-size:17px}
.band-list li{height:44px}
.band-list b{font-weight:700}
.phone-hand{left:783px;top:1158px;width:207px;height:358px;border-radius:30px;background:linear-gradient(160deg,#f2f2f2,#c9ced4)}

/* serving */
.serve-title{left:0;top:1624px;width:1200px;text-align:center;font-family:Lato,sans-serif;font-weight:900;font-size:31px;color:var(--ink)}
.serve-sub{left:0;top:1680px;width:1200px;text-align:center;font-style:italic;font-weight:600;font-size:24px;color:var(--muted)}
.serve-sub b{font-family:Lato,sans-serif;font-style:normal;font-weight:900;font-size:38px;color:var(--blue)}
.card{width:240px;height:262px;background:#f7f7f7;box-shadow:0 4px 14px rgba(0,0,0,.25);padding:16px 16px 0}
.card-photo{width:208px;height:180px}
.card-label{text-align:center;font-family:Lato,sans-serif;font-weight:700;font-size:15px;letter-spacing:1px;color:#333;margin-top:18px;text-transform:uppercase}
.card-a{left:238px;top:1790px;transform:rotate(-9deg)}
.card-b{left:484px;top:1786px;transform:rotate(2deg)}
.card-c{left:720px;top:1800px;transform:rotate(-6deg)}

/* partners */
.partners{left:98px;top:2156px;width:1004px;display:grid;grid-template-columns:repeat(5,1fr);gap:17px 17px}
.partner{height:85px;border:2px solid #dcdcdc;display:flex;align-items:center;justify-content:center;font-family:Lato,sans-serif;font-weight:700;font-size:27px;color:var(--ink)}

/* signup */
.signup{left:0;top:2532px;width:1200px;height:392px;background:linear-gradient(100deg,#3a3b3d,#23272c 60%,#3e4a57)}
.signup-title{left:0;top:2591px;width:1200px;text-align:center;font-family:Lato,sans-serif;font-weight:900;font-size:31px;color:var(--white)}
.email{left:309px;top:2660px;width:581px;height:51px;background:var(--white);display:flex;align-items:center;gap:12px;padding-left:18px;font-size:15px;color:#555}
.consent{left:309px;top:2740px;width:500px;display:flex;gap:14px;font-size:14px;line-height:24px;color:var(--white)}
.box{flex:none;width:14px;height:14px;border:1px solid var(--white);margin-top:5px;background:var(--white)}
.submit{left:538px;top:2811px;width:124px;height:47px;border-radius:24px;background:var(--blue);color:var(--white);font-weight:700;font-size:15px;display:flex;align-items:center;justify-content:center}

/* footer */
.contact{top:2985px;display:flex;align-items:center;gap:18px;font-size:14px;line-height:22px;color:#444}
.ring{width:46px;height:46px;border-radius:50%;border:1px solid #cfd8de;display:flex;align-items:center;justify-content:center}
.foot-nav{left:0;top:3064px;width:1200px;text-align:center;font-size:14px;color:#444}
.foot-rule{left:98px;top:3113px;width:1004px;height:1px;background:#e4e4e4}
.copy{left:98px;top:3140px;font-size:12px;color:#555}
.social{left:976px;top:3130px;display:flex;gap:8px}
.social span{width:38px;height:38px;border-radius:50%;border:1px solid #bcd3e3}
</style>
</head>
<body>

<div class="abs hero" role="img" aria-label="Photo of a shopper holding a smartphone in a blurred store"></div>
<div class="abs brand"><span class="brand-dot"></span><span class="brand-name">Checkora</span></div>
<nav class="abs nav"><span class="active">Home</span><span>About</span><span>Results</span><span>How</span><span>Free Trials</span>
<svg width="17" height="17" viewBox="0 0 20 20"><circle cx="8" cy="8" r="6" fill="none" stroke="#fff" stroke-width="3"/><path d="M12.5 12.5 18 18" stroke="#fff" stroke-width="3"/></svg></nav>
<h1 class="abs hero-title">Transform retail Execution<br>with a simple photo</h1>
<div class="abs dots"><span></span><span></span><span></span><span></span></div>

<section class="abs stats">
  <div class="stat"><div class="stat-num">2.2M</div><div class="stat-label">Photos reviewed last year</div></div>
  <div class="stat"><div class="stat-num">5P</div><div class="stat-label">From per photo reviewed</div></div>
  <div class="stat"><div class="stat-num">97.2%</div><div class="stat-label">Average compliance</div></div>
  <div class="stat"><div class="stat-num">3-8%</div><div class="stat-label">Sales increase</div></div>
</section>
<div class="abs stats-rule"></div>

<div class="abs founder-photo" role="img" aria-label="Portrait of the founder"></div>
<h2 class="abs founder-title">BORN OUT OF RETAIL EXECUTION</h2>
<div class="abs founder-name">Founder Marcus Delaine</div>
<ul class="abs ticks founder-list">
  <li><svg width="16" height="16" viewBox="0 0 16 16"><circle cx="8" cy="8" r="8" fill="#0792cd"/><path d="M4.5 8.2 7 10.5 11.5 5.8" fill="none" stroke="#fff" stroke-width="2"/></svg>18 years of International retail experience</li>
  <li><svg width="16" height="16" viewBox="0 0 16 16"><circle cx="8" cy="8" r="8" fill="#0792cd"/><path d="M4.5 8.2 7 10.5 11.5 5.8" fill="none" stroke="#fff" stroke-width="2"/></svg>Vice President Supply Chain Ridgewell Stores Canada</li>
  <li><svg width="16" height="16" viewBox="0 0 16 16"><circle cx="8" cy="8" r="8" fill="#0792cd"/><path d="M4.5 8.2 7 10.5 11.5 5.8" fill="none" stroke="#fff" stroke-width="2"/></svg>Innovation Director - Kelford Merchandising UK</li>
</ul>

<section class="abs band"></section>
<h2 class="abs band-title">INCREASING SALES WITH A<br>SIMPLE PHOTO &amp; DIGITAL WORKFLOW</h2>
<div class="abs band-sub">+3-8% sales with strong compliance</div>
<ul class="abs ticks band-list">
  <li><svg width="18" height="18" viewBox="0 0 16 16"><circle cx="8" cy="8" r="8" fill="#fff"/><path d="M4.5 8.2 7 10.5 11.5 5.8" fill="none" stroke="#3ca2da" stroke-width="2"/></svg><span>In <b>minutes</b> verify national promotions or range changes</span></li>
  <li><svg width="18" height="18" viewBox="0 0 16 16"><circle cx="8" cy="8" r="8" fill="#fff"/><path d="M4.5 8.2 7 10.5 11.5 5.8" fill="none" stroke="#3ca2da" stroke-width="2"/></svg><span><b>Real</b> time insights why locations are not performing</span></li>
  <li><svg width="18" height="18" viewBox="0 0 16 16"><circle cx="8" cy="8" r="8" fill="#fff"/><path d="M4.5 8.2 7 10.5 11.5 5.8" fill="none" stroke="#3ca2da" stroke-width="2"/></svg><span>Eliminate field management audits, emails, calls with a <b>digital workflow</b></span></li>
</ul>
<div class="abs phone-hand" role="img" aria-label="Hand holding a phone showing a completed visit report"></div>

<h2 class="abs serve-title">SERVING TOP RETAILERS AND BRANDS</h2>
<div class="abs serve-sub"><b>2.2m</b> Photo's verified per year</div>
<div class="abs card card-a"><div class="card-photo" role="img" aria-label="Retail store interior" style="background:linear-gradient(160deg,#e9e4dc,#9a9288)"></div><div class="card-label">Retailers</div></div>
<div class="abs card card-b"><div class="card-photo" role="img" aria-label="Hotel with a swimming pool" style="background:linear-gradient(180deg,#8fb6d9,#d9cdb8 55%,#3f9ac4)"></div><div class="card-label">Hotels</div></div>
<div class="abs card card-c"><div class="card-photo" role="img" aria-label="Row of cars at a dealership" style="background:linear-gradient(160deg,#d7d9dc,#a43a3a 55%,#2d3138)"></div><div class="card-label">Car Dealerships</div></div>

<section class="abs partners">
  <div class="partner">Parvel</div><div class="partner">Lumière Co</div><div class="partner">Aveline</div><div class="partner">Harlow</div><div class="partner">Brandwell</div>
  <div class="partner">Kestrel</div><div class="partner">Unison</div><div class="partner">Voltrix</div><div class="partner">Solenne</div><div class="partner">Tandry</div>
  <div class="partner">Ashby Reed</div><div class="partner">Fairfield</div><div class="partner">Nordelle</div><div class="partner">Corvane</div><div class="partner">Swiftline</div>
</section>

<section class="abs signup" role="img" aria-label="Person working on a laptop at a desk"></section>
<h2 class="abs signup-title">START HERE</h2>
<div class="abs email"><svg width="16" height="12" viewBox="0 0 16 12"><rect width="16" height="12" fill="#555"/><path d="M0 0 8 7 16 0" fill="none" stroke="#fff" stroke-width="1.5"/></svg>Enter Email Address</div>
<div class="abs consent"><span class="box"></span><span>Yes, I have read and agree to the Privacy Policy and agree to receive email marketing from Plumora88</span></div>
<div class="abs submit">SUBMIT</div>

<div class="abs contact" style="left:272px"><span class="ring"><svg width="14" height="18" viewBox="0 0 14 18"><path d="M7 0a7 7 0 0 0-7 7c0 5 7 11 7 11s7-6 7-11a7 7 0 0 0-7-7z" fill="#0792cd"/><circle cx="7" cy="7" r="2.5" fill="#fff"/></svg></span><span>Nam libero temp um<br>soluta nobis est eligendi optioc</span></div>
<div class="abs contact" style="left:564px"><span class="ring"><svg width="18" height="18" viewBox="0 0 24 24"><path d="M6.6 10.8a15 15 0 0 0 6.6 6.6l2.2-2.2a1 1 0 0 1 1-.25 11.4 11.4 0 0 0 3.6.57 1 1 0 0 1 1 1V20a1 1 0 0 1-1 1A17 17 0 0 1 3 4a1 1 0 0 1 1-1h3.5a1 1 0 0 1 1 1c0 1.25.2 2.45.57 3.57a1 1 0 0 1-.25 1z" fill="#0792cd"/></svg></span><span>1 800 555 0142</span></div>
<div class="abs contact" style="left:760px"><span class="ring"><svg width="18" height="13" viewBox="0 0 16 12"><rect width="16" height="12" rx="1" fill="#0792cd"/><path d="M0 0 8 7 16 0" fill="none" stroke="#fff" stroke-width="1.5"/></svg></span><span>info@checkora.com</span></div>
<nav class="abs foot-nav">Home &nbsp;|&nbsp; About &nbsp;|&nbsp; Results &nbsp;|&nbsp; How &nbsp;|&nbsp; Free Trials</nav>
<div class="abs foot-rule"></div>
<div class="abs copy">Copyrights © 2018, Checkora. All rights reserved.</div>
<div class="abs social"><span></span><span></span><span></span></div>

</body>
</html>
```